KRT Project Signage

Need a sign to be displayed in the front of properties currently under Construction or Renovation to advertise our company information. Need it to be Professional and Contemporary. We are a Design/Build Construction Company. Information should include Company Name, email, website, phone number. Attached: Logo and company brochure, also included and inspiration images

```html
<!DOCTYPE html>
<html lang="en">
<head>
<meta charset="utf-8">
<title>KRT Project Signage</title>
<link rel="stylesheet" href="https://fonts.googleapis.com/css2?family=Archivo+Black&family=Poppins:wght@500;600;700;800&display=swap">
<style>
  :root {
    --backdrop: #9aa1a8;
    --sign-white: #ffffff;
    --sign-black: #0b0b0b;
    --sign-yellow: #e6df2a;
    --ink-dark: #151515;
    --ink-navy: #0f2533;
    --ink-white: #ffffff;
    --photo-dark: #1c1c1c;
    --photo-mid: #2a2a2a;
  }
  html, body {
    margin: 0;
    padding: 0;
    width: 1200px;
    height: 2400px;
    overflow: hidden;
    background: var(--backdrop);
  }
  .site-sign {
    position: absolute;
    left: 80px;
    top: 420px;
    width: 1040px;
    height: 1560px;
    box-shadow: 0 10px 40px rgba(0,0,0,0.35);
  }
  .site-sign svg { display: block; width: 100%; height: 100%; }
  .brand-name { font-family: "Poppins", sans-serif; font-weight: 600; fill: var(--ink-dark); }
  .owner-name { font-family: "Archivo Black", sans-serif; fill: var(--ink-dark); }
  .trade-line { font-family: "Poppins", sans-serif; font-weight: 500; fill: var(--ink-navy); letter-spacing: 3px; }
  .contact-line { font-family: "Poppins", sans-serif; font-weight: 500; fill: var(--ink-white); }
  .office-label { font-family: "Poppins", sans-serif; font-weight: 700; fill: var(--sign-yellow); letter-spacing: 2px; }
  .office-number { font-family: "Poppins", sans-serif; font-weight: 700; fill: var(--ink-white); letter-spacing: 1px; }
  .mobile-number { font-family: "Poppins", sans-serif; font-weight: 800; fill: var(--ink-white); }
  .icon-disc { fill: var(--sign-yellow); }
  .icon-glyph { fill: var(--sign-black); }
  .rule { stroke: var(--sign-yellow); stroke-width: 1.5; }
</style>
</head>
<body>
  <div class="site-sign">
    <svg viewBox="0 0 778 1166" xmlns="http://www.w3.org/2000/svg">
      <defs>
        <linearGradient id="buildingTone" x1="0" y1="0" x2="1" y2="1">
          <stop offset="0" stop-color="var(--photo-mid)"/>
          <stop offset="0.5" stop-color="var(--photo-dark)"/>
          <stop offset="1" stop-color="var(--sign-black)"/>
        </linearGradient>
      </defs>

      <!-- lower contact panel -->
      <rect class="contact-panel" x="0" y="470" width="778" height="696" fill="var(--sign-black)"/>
      <rect class="building-photo" x="0" y="560" width="778" height="606" fill="url(#buildingTone)" opacity="0.55" role="img" aria-label="Dark photo of a building under construction"/>

      <!-- header panel -->
      <polygon class="header-panel" points="0,0 778,0 778,495 397,647 0,492" fill="var(--sign-white)"/>
      <polygon class="accent-wedge-left" points="0,492 265,600 0,667" fill="var(--sign-yellow)"/>
      <polygon class="accent-wedge-right" points="778,495 513,600 778,667" fill="var(--sign-yellow)"/>

      <!-- brand -->
      <circle class="brand-dot" cx="168" cy="146" r="11" fill="var(--sign-yellow)"/>
      <text class="brand-name" x="400" y="162" text-anchor="middle" font-size="40">KRT CONSTRUCTION</text>

      <!-- owner -->
      <text class="owner-name" x="389" y="365" text-anchor="middle" font-size="128" textLength="575" lengthAdjust="spacingAndGlyphs">DARREN</text>
      <text class="owner-name" x="389" y="475" text-anchor="middle" font-size="128" textLength="470" lengthAdjust="spacingAndGlyphs">HOLMES</text>
      <text class="trade-line" x="389" y="540" text-anchor="middle" font-size="44">DESIGN &amp; BUILDER</text>

      <!-- contact icons -->
      <line class="rule" x1="218" y1="690" x2="322" y2="690"/>
      <line class="rule" x1="255" y1="697" x2="322" y2="697"/>
      <line class="rule" x1="483" y1="690" x2="585" y2="690"/>
      <line class="rule" x1="483" y1="697" x2="548" y2="697"/>
      <g class="pin-icon">
        <circle class="icon-disc" cx="357" cy="694" r="32"/>
        <path class="icon-glyph" d="M357 674 a13 13 0 0 1 13 13 c0 10 -13 25 -13 25 c0 0 -13 -15 -13 -25 a13 13 0 0 1 13 -13 z M357 681 a6 6 0 1 0 0.01 0 z" fill-rule="evenodd"/>
      </g>
      <g class="mail-icon">
        <circle class="icon-disc" cx="448" cy="694" r="32"/>
        <rect class="icon-glyph" x="430" y="682" width="36" height="24" rx="2"/>
        <polyline points="431,684 448,698 465,684" fill="none" stroke="var(--sign-yellow)" stroke-width="2.5"/>
      </g>

      <!-- contact text -->
      <text class="contact-line" x="389" y="780" text-anchor="middle" font-size="37">1450 SW 8th St., Ste. 310</text>
      <text class="contact-line" x="389" y="830" text-anchor="middle" font-size="37">Coral Point, FL 33480</text>
      <text class="contact-line" x="389" y="905" text-anchor="middle" font-size="40">nolan@krtconstruction.com</text>

      <text class="office-label" x="175" y="995" font-size="36">OFFICE</text>
      <circle class="icon-disc" cx="367" cy="983" r="15"/>
      <path class="icon-glyph" d="M360 975 l4 -2 l3 6 l-3 2 a10 10 0 0 0 5 6 l2 -3 l6 3 l-2 4 c-9 1 -17 -8 -15 -16 z"/>
      <text class="office-number" x="389" y="995" font-size="36">555.210.4478</text>

      <circle class="icon-disc" cx="118" cy="1068" r="37"/>
      <path class="icon-glyph" d="M103 1050 l9 -4 l7 13 l-7 5 a22 22 0 0 0 12 13 l5 -7 l13 7 l-4 9 c-20 2 -38 -17 -35 -36 z"/>
      <text class="mobile-number" x="168" y="1098" font-size="86" textLength="545" lengthAdjust="spacingAndGlyphs">555.382.9106</text>
    </svg>
  </div>
</body>
</html>
```